Onboarding Carousel UI/UX design

We need a great UI/UX design for our onboarding carousel as attached in the PDF document. The chosen designers will be given our brand book with colors and styles to be used. The images must be focused on the content of each slide and be professional unique style (Do not use the childish cartoons we have used for placeholders)

Industry/Entity Type

Mortgage Brokerage

Number of Pages Required

5+ page

Font styles to use
Other font styles liked:
• Roboto

Requirements
Must have
• Great UI / UX design
Very relevant content of the images to match the slide
Nice to have
• Brand book

https://pv.lumorak.com/view/ed991dda-3474-4c3e-9747-882e21ba3df5-b8ca/?fullscreen

Image styles we like. Would need to be customized and made unique for us.

https://pinvarlo.com/shots/6300615-Torvane-Quillet-Illustration-Collaboration
https://meltridgestudio.co.za/software-client-style-frames
Should not have
• Do not use the childish images we have used as placeholders

```html
<!DOCTYPE html>
<html lang="en">
<head>
<meta charset="utf-8">
<title>Onboarding Carousel — Harborline Brokers Apply Online</title>
<link href="https://fonts.googleapis.com/css2?family=Roboto:wght@400;500&display=swap" rel="stylesheet">
<style>
  :root {
    --page-bg: #eef0f6;
    --screen-bg: #ffffff;
    --brand-blue: #4164e3;
    --ink: #111318;
    --ink-soft: #3a3d45;
    --dot-idle: #d5d8e0;
    --art-warm-b: #e9eefc;
    --art-cool-b: #e8edfb;
  }
  * { box-sizing: border-box; margin: 0; padding: 0; }
  html, body { width: 1200px; height: 666px; overflow: hidden; }
  body {
    background: var(--page-bg);
    font-family: "Roboto", Arial, sans-serif;
    color: var(--ink);
  }
  .carousel {
    width: 1200px; height: 666px;
    display: flex; align-items: center; justify-content: center;
    gap: 38px;
  }
  .slide {
    width: 218px; height: 408px;
    background: var(--screen-bg);
    border-radius: 4px;
    box-shadow: 0 10px 30px rgba(40, 60, 120, 0.12);
    display: flex; flex-direction: column; align-items: center;
    padding: 12px 14px 16px;
    text-align: center;
    position: relative;
  }
  .slide--device {
    width: 214px; height: 460px;
    border-radius: 18px;
    padding-top: 30px;
    padding-bottom: 26px;
  }
  .status-bar {
    position: absolute; top: 10px; left: 16px; right: 16px;
    display: flex; justify-content: space-between; align-items: center;
    font-size: 8px; font-weight: 500;
  }
  .status-bar svg { display: block; }
  .slide-art {
    width: 140px; height: 130px;
    border-radius: 10px;
  }
  .slide-art--welcome { background: linear-gradient(180deg, var(--art-warm-b), #fde6df); }
  .slide-art--email { background: linear-gradient(160deg, #fff1d6, var(--art-cool-b) 55%, #efe4fb); }
  .slide-art--security { background: linear-gradient(160deg, var(--art-cool-b), #c9d6f8); }
  .slide-title {
    margin-top: 26px;
    font-size: 15.5px; font-weight: 500; line-height: 1.3;
    letter-spacing: 0.4px;
  }
  .slide-lead {
    margin-top: 10px;
    font-size: 12.5px; line-height: 1.3;
  }
  .slide-note {
    margin-top: 12px;
    font-size: 9.5px; line-height: 1.6;
    color: var(--ink-soft);
  }
  .progress {
    display: flex; gap: 5px; align-items: center;
    margin-top: 14px;
  }
  .progress span {
    width: 4px; height: 4px; border-radius: 50%;
    background: var(--dot-idle);
  }
  .progress span.is-active {
    width: 8px; height: 8px; background: var(--brand-blue);
  }
  .login-hint {
    margin-top: 10px;
    font-size: 8.5px; color: var(--ink-soft);
  }
  .login-hint a { color: var(--brand-blue); text-decoration: none; }
  .next-button {
    margin-top: auto;
    width: 110px; height: 30px;
    border: none; border-radius: 4px;
    background: var(--brand-blue); color: #fff;
    font-family: "Roboto", Arial, sans-serif;
    font-size: 12px; font-weight: 400; letter-spacing: 0.4px;
    box-shadow: 0 4px 10px rgba(65, 100, 227, 0.3);
  }
</style>
</head>
<body>
<main class="carousel">

  <section class="slide">
    <div class="slide-art slide-art--welcome" role="img" aria-label="Illustration of a person waving hello"></div>
    <h2 class="slide-title">Welcome to Harborline Brokers Apply Online</h2>
    <p class="slide-lead">You can apply online for your next mortgage credit in about 20 minutes.</p>
    <p class="slide-note">It's easy, and we will guide you all the way. See the five simple steps that you have to take!</p>
    <div class="progress"><span class="is-active"></span><span></span><span></span><span></span><span></span><span></span><span></span></div>
    <p class="login-hint">Already have an account?<a href="#">Logon</a></p>
    <button class="next-button">Next</button>
  </section>

  <section class="slide slide--device">
    <div class="status-bar">
      <span>9:41</span>
      <svg width="24" height="8" viewBox="0 0 24 8" aria-hidden="true">
        <path d="M1 3 Q5 0 9 3 M3 5 Q5 3.5 7 5" stroke="#111318" stroke-width="1" fill="none"/>
        <circle cx="5" cy="6.8" r="0.9" fill="#111318"/>
        <rect x="12" y="1" width="10" height="6" rx="1.5" fill="#111318"/>
        <rect x="22.5" y="3" width="1" height="2" fill="#111318"/>
      </svg>
    </div>
    <div class="slide-art slide-art--email" role="img" aria-label="Illustration of a person receiving a new email notification"></div>
    <h2 class="slide-title">Create your<br>personal account</h2>
    <p class="slide-lead">You will need a valid email address to create your account</p>
    <p class="slide-note">We will send you a confirmation email, make sure you click the link to verify your email address.</p>
    <div class="progress"><span></span><span class="is-active"></span><span></span><span></span><span></span><span></span><span></span></div>
    <button class="next-button">Next</button>
  </section>

  <section class="slide">
    <div class="slide-art slide-art--security" role="img" aria-label="Illustration of a person beside a secure login panel with a key"></div>
    <h2 class="slide-title">Secure your account with your mobile phone</h2>
    <p class="slide-lead">You will need a valid mobile phone number to enable two factor authentication.</p>
    <p class="slide-note">We will send you an SMS containing a security code to verify your mobile number.</p>
    <div class="progress"><span></span><span></span><span class="is-active"></span><span></span><span></span><span></span><span></span></div>
    <button class="next-button">Next</button>
  </section>

</main>
</body>
</html>
```